Meridale Accountants needs a stationery design

We need a stationery design for our new innovative accountancy practise - it is to look professional and reliable but also minimalist, crisp, innovative and fresh. Avoid the use of block colour. You must include letterhead.

We look after business clients and help them get started and grow to successful companies. We provide a range of software, accounting, taxation and business consulting services to these clients.

This is a spin off from our more traditional existing practise - we would like to use the same green and blue.

The final design should communicate professional expertise coupled with innovative technology and personal care. The font of the type should reflect this - so far we have received standard font only.

We need business cards, letterhead, with comp slips, We need to see the whole set to form a view, not just the businesscard

I have uploaded the colours that we want to use from our existing letterhead, being the green and blue. We need to use the KTR logo - also enclosed - please use the text from the enclosed letterhead, but don't refer to this for design purposes - this was our temporary draft only.

Target Market(s)

Small to medium companies, high wealth investor clients

Industry/Entity Type

Professional Service

Requirements
Must have
• Crisp, simple design but evoking innovation, technology, competence and difference.
• So far the designs are too standard and not showing innovation.

```html
<!DOCTYPE html>
<html lang="en">
<head>
<meta charset="utf-8">
<title>Meridale Accountants – Letterhead</title>
<link href="https://fonts.googleapis.com/css2?family=PT+Sans:ital,wght@0,400;0,700;1,400&display=swap" rel="stylesheet">
<style>
  :root {
    --backdrop: #8fc0e0;
    --paper: #ffffff;
    --blue: #0a7db8;
    --blue-deep: #075f91;
    --green: #6f9a2a;
    --green-light: #9cc04a;
    --ink: #4a5561;
    --ink-soft: #6b7781;
    --badge: #1a5e9c;
  }
  * { box-sizing: border-box; margin: 0; padding: 0; }
  html, body { width: 1200px; height: 784px; overflow: hidden; }
  body {
    background: var(--backdrop);
    font-family: "PT Sans", Arial, sans-serif;
    color: var(--ink);
    position: relative;
  }
  .letterhead {
    position: absolute;
    left: 340px; top: 24px;
    width: 520px; height: 736px;
    background: radial-gradient(ellipse at 50% 45%, #ffffff 0%, #ffffff 45%, #f3f8fc 100%);
    box-shadow: 0 6px 18px rgba(20, 70, 110, 0.25);
    overflow: hidden;
  }
  .pattern {
    position: absolute;
    background: radial-gradient(ellipse at center, rgba(10,125,184,0.14) 0%, rgba(10,125,184,0.04) 60%, rgba(10,125,184,0) 100%);
  }
  .pattern--header { left: 0; top: 10px; width: 150px; height: 90px; }
  .pattern--footer { right: 40px; bottom: 40px; width: 200px; height: 110px; }

  .header-band {
    position: absolute; left: 0; top: 30px;
    width: 82px; height: 22px;
    background: linear-gradient(180deg, var(--green-light), var(--green));
  }
  .brand {
    position: absolute; left: 92px; top: 31px;
    display: flex; align-items: center; gap: 7px;
  }
  .brand__mark { width: 10px; height: 10px; background: var(--green); }
  .brand__name {
    font-size: 17px; font-weight: 400; line-height: 1; color: var(--green);
  }

  .title-bar {
    position: absolute; left: 190px; right: 0; top: 98px;
    height: 18px;
    background: linear-gradient(90deg, var(--blue-deep), var(--blue) 60%, #1a9ad6);
    color: #fff;
    font-weight: 700; font-size: 11px; letter-spacing: 2.6px;
    text-align: right; padding-right: 22px; line-height: 18px;
  }
  .liability {
    position: absolute; right: 14px; top: 122px;
    font-size: 8px; font-style: italic; color: var(--green);
  }

  .footer {
    position: absolute; left: 0; right: 0; bottom: 0; height: 150px;
  }
  .footer__rule {
    position: absolute; left: 0; top: 10px; width: 370px; height: 1px; background: var(--blue);
  }
  .footer__col { position: absolute; top: 18px; font-size: 8px; line-height: 14px; color: var(--ink-soft); }
  .footer__col::before {
    content: ""; position: absolute; left: -8px; top: -8px; width: 1px; height: 14px; background: var(--blue);
  }
  .footer__heading { font-weight: 700; font-size: 10px; color: var(--ink); margin-bottom: 3px; }
  .services { left: 30px; }
  .contact { left: 140px; }
  .icon { display: inline-block; vertical-align: -2px; margin-right: 3px; }
  .footer__stripe {
    position: absolute; left: 0; bottom: 0; width: 300px; height: 7px;
    background: linear-gradient(90deg, var(--blue), var(--blue-deep));
  }
  .footer__stripe--grey {
    left: 300px; width: 40px;
    background: linear-gradient(90deg, #b9c2c9, #eef2f5);
  }
  .member {
    position: absolute; right: 24px; bottom: 20px; width: 90px;
    display: flex; flex-direction: column; align-items: flex-start; gap: 6px;
  }
  .member__badge { width: 46px; height: 46px; background: var(--badge); }
  .member__note { font-size: 8px; color: var(--blue-deep); line-height: 11px; }
</style>
</head>
<body>
  <main class="letterhead">
    <div class="pattern pattern--header" role="img" aria-label="Soft field of faint rounded blue squares"></div>
    <div class="header-band"></div>
    <div class="brand">
      <span class="brand__mark"></span>
      <span class="brand__name">Meridale Accountants</span>
    </div>
    <div class="title-bar">Meridale Accountants</div>
    <p class="liability">Liability limited by a Scheme approved under Professional Standards Legislation</p>

    <footer class="footer">
      <div class="pattern pattern--footer" role="img" aria-label="Soft field of faint rounded blue squares"></div>
      <div class="footer__rule"></div>
      <div class="footer__col services">
        <div class="footer__heading">Services</div>
        <div><svg class="icon" width="8" height="8" viewBox="0 0 8 8"><path d="M1 1 L7 4 L1 7 Z" fill="#6f9a2a"/></svg>Tax and Accounting</div>
        <div><svg class="icon" width="8" height="8" viewBox="0 0 8 8"><path d="M1 1 L7 4 L1 7 Z" fill="#6f9a2a"/></svg>Business Development</div>
        <div><svg class="icon" width="8" height="8" viewBox="0 0 8 8"><path d="M1 1 L7 4 L1 7 Z" fill="#6f9a2a"/></svg>Superannuation and<br>&nbsp;&nbsp;&nbsp;Financial Services</div>
      </div>
      <div class="footer__col contact">
        <div class="footer__heading">Contact Details</div>
        <div><svg class="icon" width="9" height="9" viewBox="0 0 10 10"><circle cx="5" cy="5" r="4.5" fill="#0a7db8"/><circle cx="5" cy="4.3" r="1.4" fill="#fff"/></svg>Suite 4B, Level 1, 22 Harlow Street, Bremworth NSW 2590</div>
        <div><svg class="icon" width="9" height="9" viewBox="0 0 10 10"><circle cx="5" cy="5" r="4.5" fill="#0a7db8"/><rect x="3" y="2.5" width="4" height="5" rx="1" fill="#fff"/></svg>(02) 4812 6650 &nbsp;<svg class="icon" width="9" height="9" viewBox="0 0 10 10"><circle cx="5" cy="5" r="4.5" fill="#0a7db8"/><rect x="3.5" y="2" width="3" height="6" rx="0.8" fill="#fff"/></svg>0432 915 708</div>
        <div><svg class="icon" width="9" height="9" viewBox="0 0 10 10"><circle cx="5" cy="5" r="4.5" fill="#0a7db8"/><rect x="2.5" y="3" width="5" height="4" fill="#fff"/></svg>clients@meridaleaccountants.com.au</div>
        <div><svg class="icon" width="9" height="9" viewBox="0 0 10 10"><circle cx="5" cy="5" r="4.5" fill="#0a7db8"/><rect x="3" y="3" width="4" height="4" fill="#fff"/></svg>P O Box 318, Bremworth NSW 2590</div>
        <div>meridaleaccountants.com.au &nbsp;|&nbsp; ABN 52 604 219 837</div>
      </div>
      <div class="member">
        <div class="member__badge" role="img" aria-label="Professional body membership badge"></div>
        <p class="member__note">Meridale Accountants is a KTR Practise</p>
      </div>
      <div class="footer__stripe"></div>
      <div class="footer__stripe footer__stripe--grey"></div>
    </footer>
  </main>
</body>
</html>
```